Redesign Digital Lending Mobile App - Android/ Flutter

Want to re-theme an existing Digital Lending Mobile app to simplify customer journeys, as well as uplift the UI.

Most users will have small screen phones so the design needs to take that into consideration while also adapting to those with larger devices, like admins with Tablets.

Have already laid out customer journeys on Figma with guidance on how the flow of the app should be. https://www.plankora.example/board/q4ZtRm81KdWe7YhXcvBnaL/LoomKit?frame-id=3-5182&s=Jk2pQwEr7TyUi-9

Video capture of current app: https://vaultbin.example/clip/7Hx3LmQp9RtZw2KcVn4YsBd8EfGj1/play
https://vaultbin.example/clip/4PsWq8ZnTk2LrXy6MbJc3VhGd9FeA/play

The documented views for Web are also here https://docshelf.example/open?ref=3B8F2204AD7C91E5!tk8d1f6a2c4e7b90d3f5a1c8e2b6d4f9a07&cid=3b8f2204ad7c91e5&kind=file%2Cdocx&wdo=2

Target Market(s)

Kenya, Tanzania, Uganda - Africa

Industry/Entity Type

Fintech

Requirements
Must have
• Responsive for diff screens, esp. in context of smaller screen smartphone
Nice to have
• Thematic components to ensure new views can easily be adapted to these themse

```html
<!DOCTYPE html>
<html lang="en">
<head>
<meta charset="utf-8">
<title>LoomKit – Lending App Screens</title>
<link rel="stylesheet" href="https://fonts.googleapis.com/css2?family=IBM+Plex+Sans:wght@300;400;500;600;700&display=swap">
<style>
:root{
  --stage:#5f5d5e;
  --blue:#3274c6;
  --green:#479d67;
  --green-soft:#bfe8cc;
  --nav:#e2f4e8;
  --ink:#1f1f1f;
  --muted:#cfcfcf;
  --track:#ededed;
  --table:#e4edf8;
  --white:#ffffff;
  --font:"IBM Plex Sans",Arial,sans-serif;
}
*{box-sizing:border-box;margin:0;padding:0}
html,body{width:895px;height:1200px;overflow:hidden;background:var(--stage);font-family:var(--font);color:var(--ink)}
.stage{position:absolute;left:0;top:0;width:1644px;height:2204px;transform:scale(.5444);transform-origin:0 0;overflow:hidden;background:var(--stage)}
.blob{position:absolute;border-radius:50%}
.blob-green{left:-630px;top:-340px;width:1060px;height:1060px;background:var(--green)}
.blob-blue{left:1230px;top:1240px;width:1020px;height:1020px;background:var(--blue)}
.screen{position:absolute;background:var(--white);overflow:hidden}
.abs{position:absolute;line-height:1}
.center{text-align:center}
.swoosh{position:absolute;left:0;width:414px;height:200px}
.brand-dot{position:absolute;width:72px;height:72px;border-radius:50%;border:8px solid var(--blue)}
.brand-name{position:absolute;left:0;width:414px;text-align:center;font-size:38px;font-weight:700;color:var(--blue);line-height:1}
.top-icons{position:absolute;display:flex;gap:8px;color:#444}
.top-icons svg{width:30px;height:30px}
.title{left:0;width:414px;font-size:28px;font-weight:600;letter-spacing:.5px}
.title .hl{color:var(--blue)}
.rule{position:absolute;height:3px;width:30px;background:var(--green)}
.divider{position:absolute;height:1px;background:#dcdcdc}
.filters-label{left:0;width:414px;font-size:30px;font-weight:400;text-align:center}
.select{position:absolute;width:178px;height:47px;border:1.5px solid #c9c9c9;display:flex;align-items:center;justify-content:space-between;padding:0 16px 0 22px;font-size:16px;color:#333;background:var(--white)}
.select::after{content:"";border-left:5px solid transparent;border-right:5px solid transparent;border-top:6px solid #222}
.stat{position:absolute;border:4px solid var(--blue);border-radius:50%;display:flex;flex-direction:column;align-items:center;justify-content:center;text-align:center;line-height:1.05}
.stat .icon{color:var(--green)}
.stat .value{font-weight:600;color:var(--ink)}
.stat .label{font-weight:600;color:var(--ink)}
.stat-lg{width:166px;height:166px}
.stat-lg .icon{width:30px;height:30px;margin-bottom:10px}
.stat-lg .value{font-size:28px;margin-bottom:10px}
.stat-lg .label{font-size:17px}
.stat-sm{width:132px;height:132px}
.stat-sm .icon{width:26px;height:26px;margin-bottom:6px}
.stat-sm .value{font-size:21px;margin-bottom:8px}
.stat-sm .label{font-size:14px;font-weight:500}
.metric-icon{position:absolute;width:112px;height:112px;border:2px solid var(--muted);border-radius:50%;display:flex;align-items:center;justify-content:center}
.metric-icon svg{width:46px;height:46px}
.metric-label{position:absolute;left:146px;width:241px;display:flex;justify-content:space-between;font-size:17px;font-weight:500;line-height:1}
.track{position:absolute;left:143px;width:244px;height:38px;border-radius:19px;background:var(--track)}
.fill{position:absolute;top:8px;left:9px;height:22px;border-radius:11px}
.fill.green{background:var(--green)}
.fill.blue{background:var(--blue)}
.btn-next{position:absolute;width:142px;height:60px;border-radius:30px;background:var(--blue);color:var(--white);font-size:19px;font-weight:600;display:flex;align-items:center;justify-content:center}
.nav{position:absolute;left:0;width:414px;background:var(--nav);display:flex;justify-content:space-around;align-items:center;padding:0 26px;color:var(--green)}
.nav-item{width:46px;height:46px;display:flex;align-items:center;justify-content:center}
.nav-item svg{width:22px;height:22px}
.nav-item.active{background:var(--green);border-radius:50%;color:var(--white)}
.search{position:absolute;border:2px solid #cfcfcf;border-radius:26px;display:flex;align-items:center;padding-left:26px;font-size:17px;color:#444}
.search-btn{position:absolute;width:38px;height:38px;border-radius:50%;background:var(--green);color:var(--white);display:flex;align-items:center;justify-content:center}
.search-btn svg{width:20px;height:20px}
.detail-table{position:absolute;background:var(--table);padding-top:18px}
.detail-table::before{content:"";position:absolute;left:236px;top:0;bottom:0;width:1px;background:#cfd8e6}
.row{height:60px;display:flex;align-items:center;margin:0 7px;border-bottom:1px solid #d3ddeb;font-size:14px}
.row:last-child{border-bottom:0}
.row .k{width:229px;padding-left:20px;font-weight:600;letter-spacing:.2px}
.row .v{padding-left:25px;color:#333}
.row .v.ok{color:#2ea84d}
.toggle{position:absolute;display:flex;border-radius:37px;overflow:hidden;font-size:22px;font-weight:600}
.toggle span{display:flex;align-items:center;justify-content:center}
.toggle .on{background:var(--green);color:var(--white);width:189px}
.toggle .off{background:var(--green-soft);color:var(--green);flex:1;margin-left:3px}
.tabs{position:absolute;font-size:14px;font-weight:600;line-height:1}
.tabs span{position:absolute;transform:translateX(-50%)}
.tabs .cur{color:var(--blue)}
.amount{left:0;width:414px;font-size:44px;font-weight:400;letter-spacing:1px}
.chart text{font-family:var(--font)}
</style>
</head>
<body>
<svg width="0" height="0" style="position:absolute" aria-hidden="true">
  <defs>
    <symbol id="i-file" viewBox="0 0 24 24"><path fill="currentColor" d="M5 2h9v6h6v14H5z"/><path fill="currentColor" d="M15.2 2 20 6.8h-4.8z"/></symbol>
    <symbol id="i-home" viewBox="0 0 24 24"><path fill="currentColor" d="M12 3 1.5 12.5H5V21h5v-6h4v6h5v-8.5h3.5z"/></symbol>
    <symbol id="i-pencil" viewBox="0 0 24 24"><path fill="currentColor" d="M3 17.5V21h3.5L17.8 9.7l-3.5-3.5zM20.7 6.8a1 1 0 0 0 0-1.4l-2.1-2.1a1 1 0 0 0-1.4 0l-1.7 1.7 3.5 3.5z"/></symbol>
    <symbol id="i-gears" viewBox="0 0 24 24"><g fill="none" stroke="currentColor"><circle cx="9" cy="11" r="5" stroke-width="4" stroke-dasharray="2.2 1.7"/><circle cx="9" cy="11" r="3.3" stroke-width="2.6"/><circle cx="19" cy="18" r="3" stroke-width="3" stroke-dasharray="1.6 1.2"/><circle cx="19" cy="18" r="2" stroke-width="1.8"/></g></symbol>
    <symbol id="i-user" viewBox="0 0 24 24"><circle cx="12" cy="7" r="5" fill="currentColor"/><path fill="currentColor" d="M2.5 22c0-5.5 4.3-8.5 9.5-8.5s9.5 3 9.5 8.5z"/></symbol>
    <symbol id="i-users" viewBox="0 0 30 24"><circle cx="15" cy="7" r="4.5" fill="currentColor"/><circle cx="6" cy="8.5" r="3.2" fill="currentColor"/><circle cx="24" cy="8.5" r="3.2" fill="currentColor"/><path fill="currentColor" d="M7.5 21c0-5 3.4-7.5 7.5-7.5s7.5 2.5 7.5 7.5zM0 19c0-4 2.5-6 6-6 1 0 2 .2 2.7.6C7 15 6 17 6 19zM30 19c0-4-2.5-6-6-6-1 0-2 .2-2.7.6C23 15 24 17 24 19z"/></symbol>
    <symbol id="i-calendar" viewBox="0 0 24 24"><path fill="currentColor" d="M2 5h20v17H2zM6 2h3v5H6zM15 2h3v5h-3z"/><path fill="#ffffff" d="M2 9.5h20V11H2z"/></symbol>
    <symbol id="i-wallet" viewBox="0 0 24 24"><path fill="currentColor" d="M3 6h16v3h2v11H3z"/><path fill="currentColor" d="M4 3h12v2H4z"/><circle cx="17" cy="14.5" r="1.6" fill="#ffffff"/></symbol>
    <symbol id="i-calc" viewBox="0 0 24 24"><path fill="currentColor" d="M4 1h16v22H4z"/><path fill="#ffffff" d="M7 4h10v4H7zM7 11h2.5v2.5H7zM10.75 11h2.5v2.5h-2.5zM14.5 11H17v2.5h-2.5zM7 15.5h2.5V18H7zM10.75 15.5h2.5V18h-2.5zM14.5 15.5H17V18h-2.5z"/></symbol>
    <symbol id="i-case" viewBox="0 0 24 24"><path fill="currentColor" d="M8 3h8v4h-2V5h-4v2H8z"/><path fill="currentColor" d="M1 7h22v6H1zM1 14.5h22V22H1z"/><path fill="currentColor" d="M10 12h4v4h-4z"/></symbol>
    <symbol id="i-search" viewBox="0 0 24 24"><circle cx="10" cy="10" r="6" fill="none" stroke="currentColor" stroke-width="3"/><path d="m14.5 14.5 6 6" stroke="currentColor" stroke-width="3.2" stroke-linecap="round"/></symbol>
    <symbol id="i-profile" viewBox="0 0 24 24"><g fill="none" stroke="currentColor" stroke-width="1.3"><circle cx="12" cy="12" r="10.5"/><circle cx="12" cy="9.5" r="3.5"/><path d="M5.3 19c1.3-3 3.8-4.4 6.7-4.4s5.4 1.4 6.7 4.4"/></g></symbol>
    <symbol id="i-bell" viewBox="0 0 24 24"><g fill="none" stroke="currentColor" stroke-width="1.3"><path d="M5 18h14l-2-3v-5a5 5 0 0 0-10 0v5zM10 20.5a2 2 0 0 0 4 0M12 3v2"/></g><circle cx="18.5" cy="5" r="2.6" fill="#3274c6"/></symbol>
    <symbol id="swoosh" viewBox="0 0 414 200"><path fill="#3274c6" d="M0 68C90 150 220 185 414 138v12C230 200 90 175 0 92z"/><path fill="#479d67" d="M110 160c110 25 210 20 304-20v15C300 192 200 192 110 160z"/></symbol>
  </defs>
</svg>

<div class="stage">
  <div class="blob blob-green"></div>
  <div class="blob blob-blue"></div>

  <!-- Loan summary screen -->
  <section class="screen screen-summary" style="left:128px;top:122px;width:414px;height:1940px">
    <svg class="swoosh" style="top:0"><use href="#swoosh"/></svg>
    <div class="brand-dot" style="left:164px;top:12px"></div>
    <div class="brand-name" style="top:104px">LoomKit</div>
    <div class="top-icons" style="left:322px;top:27px"><svg><use href="#i-profile"/></svg><svg><use href="#i-bell"/></svg></div>

    <h1 class="abs title center" style="top:227px"><span class="hl">LOAN SUMMARY</span></h1>
    <h2 class="abs title center" style="top:261px">1 MONTH PERIOD</h2>
    <div class="rule" style="left:192px;top:298px"></div>

    <div class="stat stat-lg" style="left:26px;top:325px"><svg class="icon"><use href="#i-file"/></svg><div class="value">$30,000</div><div class="label">DISBURSED</div></div>
    <div class="stat stat-lg" style="left:220px;top:325px"><div class="icon" style="width:auto;height:auto;font-size:38px;font-weight:700;line-height:1;margin-bottom:4px">$$</div><div class="value">$10,000</div><div class="label">COLLECTED</div></div>
    <div class="stat stat-lg" style="left:26px;top:505px"><svg class="icon"><use href="#i-user"/></svg><div class="value">432</div><div class="label">ACTIVE<br>CLIENTS</div></div>
    <div class="stat stat-lg" style="left:220px;top:505px"><svg class="icon" style="width:40px"><use href="#i-users"/></svg><div class="value">23</div><div class="label">NEW<br>CLIENTS</div></div>

    <div class="divider" style="left:12px;top:714px;width:390px"></div>
    <h3 class="abs filters-label" style="top:751px">FILTERS</h3>
    <div class="select" style="left:23px;top:807px">Loan Officer</div>
    <div class="select" style="left:213px;top:807px">Branch</div>
    <div class="select" style="left:23px;top:867px">Fund</div>
    <div class="select" style="left:213px;top:867px">Product</div>

    <div class="metric-icon" style="left:24px;top:948px;color:var(--green)"><svg><use href="#i-calendar"/></svg></div>
    <div class="metric-label" style="top:969px"><span>Near Due</span><span>$ 25,00,000</span></div>
    <div class="track" style="top:1000px"><div class="fill green" style="width:92px"></div></div>

    <div class="metric-icon" style="left:24px;top:1067px;color:var(--blue);font-size:64px;font-weight:700">$</div>
    <div class="metric-label" style="top:1088px"><span>Due</span><span>$ 35,000</span></div>
    <div class="track" style="top:1119px"><div class="fill blue" style="width:162px"></div></div>

    <div class="metric-icon" style="left:24px;top:1187px;color:var(--green)"><svg><use href="#i-file"/></svg></div>
    <div class="metric-label" style="top:1208px"><span>Pending Disbursement</span><span>$200</span></div>
    <div class="track" style="top:1239px"><div class="fill green" style="width:92px"></div></div>

    <div class="metric-icon" style="left:24px;top:1306px;color:var(--blue)"><svg><use href="#i-pencil"/></svg></div>
    <div class="metric-label" style="top:1327px"><span>Active Loans</span><span>$ 20,000</span></div>
    <div class="track" style="top:1358px"><div class="fill blue" style="width:162px"></div></div>

    <h3 class="abs" style="left:47px;top:1452px;font-size:28px;font-weight:700">REPORTS</h3>
    <svg class="chart" style="position:absolute;left:30px;top:1500px;width:380px;height:240px" viewBox="158 1622 380 240">
      <g font-size="13" fill="#222" text-anchor="end">
        <text x="197" y="1661">100</text><text x="189" y="1704">75</text><text x="189" y="1747">50</text><text x="189" y="1790">25</text><text x="181" y="1833">0</text>
      </g>
      <g font-size="13" fill="#222" text-anchor="middle">
        <text x="232" y="1849">JAN</text><text x="281" y="1849">FEB</text><text x="330" y="1849">MAR</text><text x="380" y="1849">APR</text><text x="429" y="1849">MAY</text><text x="479" y="1849">JUN</text>
      </g>
      <path d="M211 1630v198h284" fill="none" stroke="#555" stroke-width="1.5"/>
      <path d="M213 1760h237" stroke="var(--green)" stroke-dasharray="5 5" stroke-width="1"/>
      <polyline points="213,1743 248,1725 269,1782 300,1750 345,1808 352,1713 380,1760 450,1686" fill="none" stroke="var(--green)" stroke-width="2"/>
    </svg>

    <div class="btn-next" style="left:136px;top:1773px">NEXT</div>
    <nav class="nav" style="top:1866px;height:74px">
      <span class="nav-item active"><svg><use href="#i-home"/></svg></span>
      <span class="nav-item"><svg><use href="#i-file"/></svg></span>
      <span class="nav-item"><svg><use href="#i-pencil"/></svg></span>
      <span class="nav-item"><svg><use href="#i-gears"/></svg></span>
    </nav>
  </section>

  <!-- Summary details screen -->
  <section class="screen screen-details" style="left:626px;top:122px;width:414px;height:1420px">
    <svg class="swoosh" style="top:40px"><use href="#swoosh"/></svg>
    <div class="brand-dot" style="left:164px;top:52px"></div>
    <div class="brand-name" style="top:144px">LoomKit</div>
    <div class="top-icons" style="left:322px;top:67px"><svg><use href="#i-profile"/></svg><svg><use href="#i-bell"/></svg></div>

    <h1 class="abs title center" style="top:267px"><span class="hl">SUMMARY</span> DETAILS</h1>
    <div class="rule" style="left:192px;top:308px"></div>

    <div class="search" style="left:24px;top:342px;width:368px;height:51px">Search</div>
    <div class="search-btn" style="left:345px;top:349px"><svg><use href="#i-search"/></svg></div>

    <div class="divider" style="left:22px;top:434px;width:372px"></div>
    <h3 class="abs filters-label" style="top:471px">FILTERS</h3>
    <div class="select" style="left:24px;top:528px">Loan Officer</div>
    <div class="select" style="left:213px;top:528px">Branch</div>
    <div class="select" style="left:24px;top:588px">Fund</div>
    <div class="select" style="left:213px;top:588px">Product</div>

    <div class="detail-table" style="left:22px;top:656px;width:371px;height:570px">
      <div class="row"><span class="k">LOAN REFERENCE NUMBER</span><span class="v">2344</span></div>
      <div class="row"><span class="k">LOAN STATUS</span><span class="v ok">Active</span></div>
      <div class="row"><span class="k">DATE DISBURSED</span><span class="v">13/July 2024</span></div>
      <div class="row"><span class="k">DATE APPROVED</span><span class="v">20 July 2024</span></div>
      <div class="row"><span class="k">LAST REPAYMENT DATE</span><span class="v">27 July 2024</span></div>
      <div class="row"><span class="k">NEXT REPAYMENT DATE</span><span class="v">27 July 2024</span></div>
      <div class="row"><span class="k">AMOUNT DISBURSED</span><span class="v">30,000</span></div>
      <div class="row"><span class="k">AMOUNT OUTSTANDING</span><span class="v">30,000</span></div>
      <div class="row"><span class="k">OVERDUE DAYS</span><span class="v">30</span></div>
    </div>

    <div class="btn-next" style="left:136px;top:1254px">NEXT</div>
    <nav class="nav" style="top:1346px;height:74px">
      <span class="nav-item"><svg><use href="#i-home"/></svg></span>
      <span class="nav-item active"><svg><use href="#i-file"/></svg></span>
      <span class="nav-item"><svg><use href="#i-pencil"/></svg></span>
      <span class="nav-item"><svg><use href="#i-gears"/></svg></span>
    </nav>
  </section>

  <!-- Total loan screen -->
  <section class="screen screen-total" style="left:1123px;top:122px;width:414px;height:1380px">
    <svg class="swoosh" style="top:0"><use href="#swoosh"/></svg>
    <div class="brand-dot" style="left:164px;top:12px"></div>
    <div class="brand-name" style="top:104px">LoomKit</div>
    <div class="top-icons" style="left:322px;top:27px"><svg><use href="#i-profile"/></svg><svg><use href="#i-bell"/></svg></div>

    <h1 class="abs title center" style="top:227px"><span class="hl">TOTAL</span> LOAN</h1>
    <div class="rule" style="left:192px;top:268px"></div>
    <div class="abs amount center" style="top:299px">$ 35,00,000</div>

    <div class="divider" style="left:12px;top:394px;width:390px"></div>
    <h3 class="abs filters-label" style="top:431px">FILTERS</h3>
    <div class="select" style="left:23px;top:487px">Loan Officer</div>
    <div class="select" style="left:213px;top:487px">Branch</div>
    <div class="select" style="left:23px;top:547px">Fund</div>
    <div class="select" style="left:213px;top:547px">Product</div>

    <div class="toggle" style="left:34px;top:622px;width:356px;height:74px"><span class="on">PROFIT</span><span class="off">LOSS</span></div>
    <div class="tabs" style="left:0;top:716px;width:414px">
      <span style="left:93px">DAY</span><span class="cur" style="left:154px">WEEK</span><span style="left:235px">MONTHLY</span><span style="left:315px">YEAR</span>
    </div>

    <svg class="chart" style="position:absolute;left:17px;top:738px;width:370px;height:275px" viewBox="1140 860 370 275">
      <rect x="1183" y="866" width="319" height="238" fill="none" stroke="#333" stroke-width="1"/>
      <g font-size="10" fill="#222" text-anchor="end">
        <text x="1175" y="880">1.00</text><text x="1175" y="907">0.75</text><text x="1175" y="934">0.50</text><text x="1175" y="961">0.25</text><text x="1175" y="988">0.00</text><text x="1175" y="1016">−0.25</text><text x="1175" y="1043">−0.50</text><text x="1175" y="1070">−0.75</text><text x="1175" y="1097">−1.00</text>
      </g>
      <g font-size="12" fill="#222" text-anchor="middle">
        <text x="1201" y="1124">Week 1</text><text x="1268" y="1124">Week 2</text><text x="1335" y="1124">Week 3</text><text x="1402" y="1124">Week 4</text><text x="1469" y="1124">Week 5</text>
      </g>
      <path d="M1336 877v226" stroke="var(--green)" stroke-width="1"/>
      <polyline points="1190,1100 1230,1099 1260,1086 1280,1050 1300,978 1315,917 1325,888 1335,877 1345,888 1355,917 1370,978 1390,1050 1410,1086 1440,1099 1470,1100" fill="none" stroke="var(--green)" stroke-width="1.4"/>
    </svg>

    <div class="stat stat-sm" style="left:65px;top:1019px"><div class="icon" style="width:auto;height:auto;font-size:36px;font-weight:700;line-height:1;margin-bottom:2px">$</div><div class="value">$30,000</div><div class="label">REVENUE</div></div>
    <div class="stat stat-sm" style="left:217px;top:1019px"><svg class="icon"><use href="#i-wallet"/></svg><div class="value">$10,000</div><div class="label">EXPENSES</div></div>
    <div class="stat stat-sm" style="left:65px;top:1160px"><svg class="icon"><use href="#i-calc"/></svg><div class="value">432</div><div class="label">TAX</div></div>
    <div class="stat stat-sm" style="left:217px;top:1160px"><svg class="icon"><use href="#i-case"/></svg><div class="value">23</div><div class="label">SALARIES</div></div>

    <nav class="nav" style="top:1308px;height:72px">
      <span class="nav-item"><svg><use href="#i-home"/></svg></span>
      <span class="nav-item"><svg><use href="#i-file"/></svg></span>
      <span class="nav-item active"><svg><use href="#i-pencil"/></svg></span>
      <span class="nav-item"><svg><use href="#i-gears"/></svg></span>
    </nav>
  </section>
</div>
</body>
</html>
```